Calvanto Group Real Estate Company business cards

New business card design, we are generally happy with the basic layout of the existing front of business card, (feel free to change) but require a head shot photo on the back side.

http://www.calvanto.com.au/

Attached logos, and existing business card

------------------------------

Target Market(s)

Real estate

Industry/Entity Type

Real Estate

Contact Information for Business Card

Standard size double sided

Font styles to use
Other font styles liked:
• Futura

Requirements
Must have
• Photo head shot on the back side
Nice to have
• yes
Should not have
• No

```html
<!DOCTYPE html>
<html lang="en">
<head>
<meta charset="utf-8">
<title>Calvanto Group – Business Cards</title>
<link rel="stylesheet" href="https://fonts.googleapis.com/css2?family=Source+Sans+3:wght@400;600;700&family=Roboto+Condensed:wght@700&display=swap">
<style>
  :root {
    --stage: #3b3b3b;
    --paper: #f7f7f7;
    --purple: #2e1c5f;
    --orange: #f0871f;
    --ink: #333333;
    --rule: #e2b07a;
    --white: #ffffff;
  }
  * { margin: 0; padding: 0; box-sizing: border-box; }
  html, body { width: 1200px; height: 750px; overflow: hidden; }
  body {
    background: var(--stage);
    font-family: "Source Sans 3", sans-serif;
    position: relative;
  }
  .card {
    position: absolute;
    top: 228px;
    width: 461px;
    height: 262px;
    overflow: hidden;
  }
  .card--front { left: 124px; background: var(--paper); }
  .card--back  { left: 618px; background: var(--purple); }

  /* front */
  .brand {
    position: absolute;
    right: 31px;
    top: 30px;
    width: 180px;
    text-align: center;
  }
  .brand__name {
    font-size: 40px;
    font-weight: 400;
    color: var(--purple);
    line-height: 1;
    letter-spacing: 0.5px;
  }
  .brand__services {
    margin-top: 14px;
    font-family: "Roboto Condensed", sans-serif;
    font-weight: 700;
    font-size: 11px;
    color: var(--purple);
    word-spacing: 6px;
  }
  .marker {
    position: absolute;
    left: 0; top: 141px;
    width: 9px; height: 33px;
    background: var(--purple);
  }
  .person__name {
    position: absolute;
    left: 23px; top: 138px;
    font-size: 18.5px;
    font-weight: 600;
    color: var(--purple);
  }
  .person__title {
    position: absolute;
    left: 23px; top: 159px;
    font-size: 13px;
    color: var(--orange);
  }
  .rule {
    position: absolute;
    left: 73px; top: 171px;
    width: 361px; height: 1px;
    background: var(--rule);
  }
  .contacts {
    position: absolute;
    left: 25px; top: 186px;
    list-style: none;
  }
  .contacts li {
    display: flex;
    align-items: center;
    height: 18px;
    font-size: 12.5px;
    color: var(--ink);
  }
  .contacts svg { width: 12px; height: 12px; margin-right: 6px; fill: var(--purple); }
  .company {
    position: absolute;
    right: 24px; top: 204px;
    text-align: right;
    color: var(--ink);
    line-height: 17px;
  }
  .company__name { font-size: 13.5px; font-weight: 600; }
  .company__abn  { font-size: 12.5px; }
  .band {
    position: absolute;
    left: 0; bottom: 0;
    width: 100%; height: 8px;
    background: var(--purple);
  }
  .band__accent {
    position: absolute;
    left: 72px; top: 0;
    width: 133px; height: 100%;
    background: var(--orange);
  }

  /* back */
  .back__brand {
    position: absolute;
    left: 35px; top: 150px;
    font-size: 46px;
    font-weight: 600;
    color: var(--orange);
    line-height: 1;
  }
  .back__web {
    position: absolute;
    left: 35px; top: 231px;
    font-size: 12px;
    letter-spacing: 1.6px;
    color: var(--white);
  }
  .headshot {
    position: absolute;
    left: 276px; top: 14px;
    width: 186px; height: 248px;
    background: linear-gradient(180deg, #3a3350 0%, #2b3a64 55%, #24345c 100%);
  }
</style>
</head>
<body>
  <section class="card card--front">
    <div class="brand">
      <div class="brand__name">calvanto</div>
      <div class="brand__services">Buy | Sell | Rent</div>
    </div>

    <div class="marker"></div>
    <div class="person__name">Daniel Tran</div>
    <div class="person__title">Director</div>
    <div class="rule"></div>

    <ul class="contacts">
      <li>
        <svg viewBox="0 0 24 24" aria-hidden="true"><path d="M6.6 10.8a15.2 15.2 0 0 0 6.6 6.6l2.2-2.2c.3-.3.7-.4 1-.2 1.1.4 2.3.6 3.6.6.6 0 1 .4 1 1V20c0 .6-.4 1-1 1A17 17 0 0 1 3 4c0-.6.4-1 1-1h3.5c.6 0 1 .4 1 1 0 1.3.2 2.5.6 3.6.1.3 0 .7-.2 1z"/></svg>
        0412 555 308
      </li>
      <li>
        <svg viewBox="0 0 24 24" aria-hidden="true"><path d="M2 5h20v14H2z M2 5l10 8 10-8" fill="none" stroke="#2e1c5f" stroke-width="2.4"/></svg>
        daniel.tran@calvanto.com.au
      </li>
      <li>
        <svg viewBox="0 0 24 24" aria-hidden="true"><circle cx="12" cy="12" r="10"/><path d="M7 7c2 1 3 3 2 5s1 3 3 3M15 5c-1 2 0 3 2 4s2 3 1 5" fill="none" stroke="#f7f7f7" stroke-width="1.6"/></svg>
        www.calvanto.com.au
      </li>
    </ul>

    <div class="company">
      <div class="company__name">Calvanto Group</div>
      <div class="company__abn">ABN: 12 345 678 901</div>
    </div>

    <div class="band"><div class="band__accent"></div></div>
  </section>

  <section class="card card--back">
    <div class="back__brand">calvanto</div>
    <div class="back__web">www.calvanto.com.au</div>
    <div class="headshot" role="img" aria-label="Head shot photo of the director in a navy suit and blue tie"></div>
  </section>
</body>
</html>
```